http://www.brindlewares.com/ New Ecommerce Site

We are redesigning Brindlewares.com on shopvantly.com.

We need to get a design for the ecommerce site.

They have about 15-45 products and these are the menu items that they need on the pages.

Knives:
Kitchen Knives
Neck Knives
Outdoor Knives
Bluefinch Knives
Clearance Knives
Premium Knives
Misc. Product:
Waterstones
Books
DVDs
T-Shirts
Scissors
Bladesmithing School
Videos
Links
Testimonials/Feedback
Contact Dennis Form
Knife Care and Maintenance Tips
Knife Sharpening
Knife Archives
Kitchen Knife Archives

We need several pages designed.

- Category Page
- Single Item page
- Knive Archive Pages (This is where old knives are stored that are not being sold anymore)
- Featured Product pages.
- Information pages
- checkout

The design has to be VERY elagant, like vostel.com.
And it has to be very easy to navigate and buy items like http://bladesgoquick.com/

Thanks,
Peter Hollis

Requirements
Must have
• Must be very elegant, and have the menu items somewhere on the pages.

```html
<!DOCTYPE html>
<html lang="en">
<head>
<meta charset="utf-8">
<title>Brindlewares – Hand-forged Cutlery</title>
<link rel="stylesheet" href="https://fonts.googleapis.com/css2?family=PT+Sans:wght@400;700&family=Questrial&display=swap">
<style>
:root{
  --orange:#e8731a;
  --orange-light:#f59a2a;
  --brown:#6b3612;
  --grey-nav:#8b8b8b;
  --grey-panel:#8e8e8e;
  --ink:#333;
  --muted:#777;
  --footer:#2b2b2b;
  --line:#dcdcdc;
  --white:#fff;
}
*{box-sizing:border-box;margin:0;padding:0}
html,body{width:972px;height:1200px;overflow:hidden;background:#fff}
body{font-family:"PT Sans",sans-serif;color:var(--ink)}
.page{position:relative;width:1200px;height:1481px;transform:scale(0.81);transform-origin:0 0;background:#fff}
.abs{position:absolute}
.header{left:0;top:0;width:1200px;height:136px;background:linear-gradient(#fbfbfb,#e9e9e9)}
.brand{left:108px;top:22px;font-size:52px;color:#9a9a9a;letter-spacing:1px;line-height:1}
.brand-tag{left:109px;top:110px;font-size:13px;color:#666}
.phone{left:903px;top:44px;display:flex;align-items:center;gap:6px;color:var(--orange);font-size:26px}
.phone-icon{width:25px;height:25px;background:var(--orange);border-radius:4px;display:flex;align-items:center;justify-content:center}
.search{left:903px;top:86px;width:174px;height:31px;background:#fff;border-radius:6px;box-shadow:0 1px 2px rgba(0,0,0,.12);font-size:14px;color:#888;padding:7px 11px}
.search svg{position:absolute;right:9px;top:5px}
.nav{left:0;top:136px;width:1200px;height:67px;background:linear-gradient(#7d7d7d,#959595)}
.nav ul{list-style:none;display:flex;position:absolute;left:134px;top:25px;gap:0}
.nav li{color:#fff;font-size:18px;margin-right:44px}
.cart{left:916px;top:152px;width:157px;height:41px;background:#6f6f6f;border-radius:6px;color:#fff;font-size:19px;display:flex;align-items:center;padding-left:12px;gap:14px}
.quick-order{left:1167px;top:210px;width:33px;height:124px;background:#111;border-radius:8px 0 0 8px;color:#fff;font-size:16px;writing-mode:vertical-rl;display:flex;align-items:center;justify-content:center}
.box{border:1px solid var(--line);background:#fff}
.welcome{left:104px;top:207px;width:153px;height:227px;padding:4px}
.welcome-inner{background:var(--grey-panel);height:100%;padding:12px 9px;color:#fff;text-align:center}
.welcome h2{font-family:"Questrial",sans-serif;font-weight:400;font-size:17px;line-height:24px}
.welcome p{font-size:11.5px;line-height:18px;text-align:justify;margin-top:10px}
.btn{background:linear-gradient(var(--orange-light),var(--orange));color:#fff;border-radius:5px;display:inline-block}
.welcome .btn{font-size:14px;padding:3px 12px;margin-top:9px}
.guarantee{left:104px;top:442px;width:153px;height:218px;padding:14px 8px 0 10px}
.guarantee h3{font-family:"Questrial",sans-serif;font-weight:400;color:#d5391a;font-size:17px;text-align:center}
.guarantee p{font-size:11.5px;line-height:18px;text-align:justify;margin-top:14px;color:#222}
.slider{left:265px;top:207px;width:571px;height:453px;padding:3px}
.slide-photo{width:563px;height:445px;background:radial-gradient(ellipse at 55% 40%,#dcdcdc 0%,#b89a83 22%,#6b3a28 45%,#a2856a 70%,#8c7258 100%)}
.caption{left:269px;top:510px;width:563px;height:100px;background:rgba(20,20,20,.8);color:#fff;font-family:"Questrial",sans-serif;font-size:13.5px;line-height:24px;padding:37px 52px}
.arrow{width:33px;height:33px;border-radius:50%;background:#eee}
.subscribe{left:845px;top:207px;width:251px;height:344px;padding:4px 8px}
.subscribe h3{font-weight:400;font-size:22px;color:#222}
.subscribe h3 span{font-family:Georgia,serif;font-weight:700;color:var(--orange-light)}
.subscribe h4{font-weight:400;font-size:17px;color:#222;margin-top:2px}
.subscribe p{font-size:12.5px;line-height:18px;margin-top:17px;color:#222}
.field{border:1px solid #ccc;height:30px;margin-top:6px;font-size:12px;color:#999;padding:6px 10px;width:220px;margin-left:3px}
.subscribe .btn{width:215px;height:26px;margin:8px 0 0 7px;text-align:center;font-size:15px;font-weight:700;line-height:26px;border-radius:8px}
.subscribe .note{font-size:12px;line-height:18px;text-align:justify;margin:17px 6px 0;color:#333}
.products-head{left:845px;top:563px;width:251px;height:92px;background:#fff;border:1px solid var(--line)}
.products-head span{position:absolute;left:25px;top:30px;font-family:"Questrial",sans-serif;font-size:26px;color:#555}
.products-head .tab{position:absolute;right:-1px;top:-1px;width:71px;height:92px;background:linear-gradient(var(--orange-light),var(--orange))}
.cat-list{left:845px;top:655px;width:251px;height:522px;background:var(--orange);list-style:none;padding:0}
.cat-list li{height:36px;line-height:36px;padding-left:38px;color:#fff;font-size:17px}
.cat-list li.active{background:var(--brown);height:48px;line-height:48px}
.popular{left:111px;top:672px;font-family:"Questrial",sans-serif;font-size:19px;color:#111}
.popular em{font-style:normal;color:var(--orange);font-size:23px}
.product{width:233px;height:211px;border:1px solid var(--line)}
.product .photo{width:100%;height:168px}
.product .bar{position:absolute;left:0;bottom:0;width:100%;height:42px;background:#2a2a2a;display:flex;align-items:center;padding-left:20px;gap:12px;color:#fff;font-weight:700;font-size:16px}
.product .btn{font-size:12px;font-weight:400;padding:6px 11px;border-radius:4px}
.features{left:116px;top:1182px;width:962px;height:90px;border:1px solid #ccc;border-radius:10px}
.feature{position:absolute;display:flex;align-items:center;gap:14px;color:var(--orange);font-family:"Questrial",sans-serif;font-size:24px;line-height:28px}
.feature .icon{border-radius:4px}
.footer{left:0;top:1295px;width:1200px;height:186px;background:var(--footer);color:#fff;font-size:14px}
.footer h5{position:absolute;font-size:14px;font-weight:700;top:32px}
.footer a{color:#fff;text-decoration:none}
.footer .col a{display:block;line-height:24px}
.social{position:absolute;left:539px;top:64px;display:flex;gap:13px}
.social span{width:33px;height:33px;background:#4b8bc9;border-radius:4px}
.foot-brand{position:absolute;left:910px;top:20px;color:#777;font-size:36px;line-height:1}
.foot-tag{position:absolute;left:911px;top:91px;color:#777;font-size:10px}
</style>
</head>
<body>
<div class="page">

  <header class="header abs">
    <div class="brand abs">Brindlewares</div>
    <div class="brand-tag abs">17th Generation Hanamura Bladesmith</div>
    <div class="phone abs">
      <span class="phone-icon"><svg width="14" height="16" viewBox="0 0 14 16"><path d="M3 1c1 0 2 3 2 4s-2 1-1 3 2 4 4 4 1-2 2-2 3 1 3 2-1 3-3 3C6 15 1 9 1 4 1 2 2 1 3 1z" fill="#fff"/></svg></span>
      1300 555 019
    </div>
    <div class="search abs">Search
      <svg width="22" height="22" viewBox="0 0 22 22"><circle cx="9" cy="9" r="6.5" fill="none" stroke="#4a6d9a" stroke-width="2"/><path d="M14 14l6 6" stroke="#444" stroke-width="3" stroke-linecap="round"/></svg>
    </div>
  </header>

  <nav class="nav abs">
    <ul><li>Home</li><li>Knives</li><li>Tools</li><li>Instruction</li><li>About</li><li>Contact Dennis</li></ul>
  </nav>
  <div class="cart abs">
    <svg width="38" height="26" viewBox="0 0 38 26"><path d="M2 3h6l5 14h18l4-10H11" fill="none" stroke="#ccc" stroke-width="2.5"/><circle cx="15" cy="22" r="2.5" fill="#ccc"/><circle cx="29" cy="22" r="2.5" fill="#ccc"/></svg>
    Your Cart
  </div>
  <div class="quick-order abs">Quick Order</div>

  <section class="welcome box abs">
    <div class="welcome-inner">
      <h2>Welcome to Brindlewares</h2>
      <p>your source of high performance hand-forged cutlery and world renowned sharp-ening instruction!</p>
      <span class="btn">Read more</span>
    </div>
  </section>

  <section class="guarantee box abs">
    <h3>Guarantee !</h3>
    <p>Lorem ipsum dolor sit amet, consectetur adipis-icing elit, sed do eiusmod tempor incididunt ut labore et dolore magna aliqua. Ut enim ad minim veniam,</p>
  </section>

  <section class="slider box abs">
    <div class="slide-photo" role="img" aria-label="Hunting knife with antler handle resting on a tooled leather sheath"></div>
  </section>
  <div class="caption abs">Lorem ipsum dolor sit amet, consectetur adipisicing elit, sed do eiusmod tempor incididunt ut labore et dolore magna aliqua.</div>
  <svg class="abs" style="left:282px;top:556px" width="33" height="33" viewBox="0 0 33 33"><circle cx="16.5" cy="16.5" r="16.5" fill="#e6e6e6"/><path d="M19 10l-7 6.5 7 6.5z" fill="#333"/></svg>
  <svg class="abs" style="left:783px;top:556px" width="33" height="33" viewBox="0 0 33 33"><circle cx="16.5" cy="16.5" r="16.5" fill="#e6e6e6"/><path d="M14 10l7 6.5-7 6.5z" fill="#333"/></svg>

  <aside class="subscribe box abs">
    <h3>Read your <span>FREE</span></h3>
    <h4>Knife Care Tips</h4>
    <p>Subscribe for Dennis's Free Knife Care and Maintenance Tips:</p>
    <div style="margin-top:22px">
      <div class="field">Name</div>
      <div class="field" style="margin-top:3px">Email</div>
    </div>
    <div class="btn">Subscribe Now</div>
    <p class="note">Brindlewares never shares with third parties any names and email addresses collected from this website, period! You have my name on that!</p>
  </aside>

  <div class="products-head abs">
    <span>Our products</span>
    <div class="tab"><svg style="position:absolute;left:14px;top:38px" width="42" height="24" viewBox="0 0 42 24"><path d="M3 3l18 15 18-15" fill="none" stroke="#fff" stroke-width="6"/></svg></div>
  </div>
  <ul class="cat-list abs">
    <li class="active">Kitchen Knives</li><li>Neck Knives</li><li>Outdoor Knives</li><li>Bluefinch Knives</li><li>Clearance Knives</li><li>Premium Knives</li><li>Misc. Product:</li><li>Waterstones</li><li>Books</li><li>DVDs</li><li>T-Shirts</li><li>Scissors</li><li>Bladesmithing School</li><li>Videos</li>
  </ul>

  <h2 class="popular abs" style="font-weight:400">VIEW OUR MOST POPULAR <em>Kitchen Knives</em></h2>

  <div class="product abs" style="left:109px;top:707px"><div class="photo" role="img" aria-label="Kitchen knife on a burl wood board" style="background:linear-gradient(135deg,#d9a866,#b67a3c)"></div><div class="bar">Price : $244.00 <span class="btn">Add to Cart</span></div></div>
  <div class="product abs" style="left:358px;top:707px"><div class="photo" role="img" aria-label="Knife with leather sheath" style="background:linear-gradient(135deg,#fff,#c9c9c9 55%,#8a4a2a)"></div><div class="bar">Price : $244.00 <span class="btn">Add to Cart</span></div></div>
  <div class="product abs" style="left:607px;top:707px"><div class="photo" role="img" aria-label="Set of kitchen knives with vegetables" style="background:linear-gradient(90deg,#c79a6a,#e2c19a,#b98a5a)"></div><div class="bar">Price : $244.00 <span class="btn">Add to Cart</span></div></div>
  <div class="product abs" style="left:109px;top:938px"><div class="photo" role="img" aria-label="Bowie knife on a worn sheath" style="background:linear-gradient(135deg,#cfcac4,#6a5a4e)"></div><div class="bar">Price : $244.00 <span class="btn">Add to Cart</span></div></div>
  <div class="product abs" style="left:358px;top:938px"><div class="photo" role="img" aria-label="Knife with bone handle on a brown sheath" style="background:linear-gradient(135deg,#fff,#8a3a22 50%,#e8e8e8)"></div><div class="bar" style="padding-left:22px">Price : $244.00 <span class="btn">Add to Cart</span></div></div>
  <div class="product abs" style="left:607px;top:938px"><div class="photo" role="img" aria-label="Knife with wooden handle on a dark background" style="background:linear-gradient(135deg,#3e5552,#2a3a38 60%,#b89a6c)"></div><div class="bar">Price : $244.00 <span class="btn">Add to Cart</span></div></div>

  <section class="features abs">
    <div class="feature" style="left:28px;top:14px"><div class="icon" role="img" aria-label="Sharpening DVD disc" style="width:62px;height:62px;border-radius:50%;background:radial-gradient(#fff 15%,#d8d8d8 20%,#b5b5b5)"></div><span>Advanced Blade<br>Sharpening DVD</span></div>
    <div class="feature" style="left:372px;top:14px"><div class="icon" role="img" aria-label="Kitchen knife" style="width:66px;height:62px;background:linear-gradient(135deg,#fff 30%,#bfbfbf 55%,#222 70%,#fff 72%)"></div><span>Neck Knives &amp;<br>Kitchen Cutlery</span></div>
    <div class="feature" style="left:712px;top:18px"><div class="icon" role="img" aria-label="Gear settings icon" style="width:60px;height:52px;background:linear-gradient(#9a9a9a,#4a4a4a)"></div><span>Custom Knives</span></div>
  </section>

  <footer class="footer abs">
    <h5 style="left:107px">QUICK LINKS</h5>
    <div class="col abs" style="left:108px;top:57px"><a>Home</a><a>Knives</a><a>Tools</a></div>
    <div class="col abs" style="left:249px;top:57px"><a>Instruction</a><a>About</a><a>Contact Dennis</a></div>
    <h5 style="left:538px">FOLLOW US ON</h5>
    <div class="social"><span></span><span></span><span></span></div>
    <div class="abs" style="left:538px;top:115px">Friendsly &nbsp;|&nbsp; Chirper &nbsp;|&nbsp; Linkwork</div>
    <div class="foot-brand">Brindlewares</div>
    <div class="foot-tag">17th Generation Hanamura Bladesmith</div>
    <div class="abs" style="left:776px;top:115px;color:#ddd">Copyright © 2013 &nbsp; Brindlewares. &nbsp; All rights reserved.</div>
  </footer>

</div>
</body>
</html>
```